Präsentationsvorlagen für Unternehmensberatung im Finanzbereich
Zielgruppe
Unternehmensberatung für den Finanzbereich, Compliance Beratung/Implementierung regulatorischer Projekte, Bereitstellung von Management Resourcen, Trainings/Coaching/Seminare. Zielgruppe: Banken, Fonds und Investmentgesellschaften
Aufgabenstellung
hochwertiges design, clean, keine standard bilder von Bergen, Tastaturen oder Menschen, die sich unterhalten. eher Architektur Bilder, Bilder sollen Bezug zum Inhalt haben, Verlässlichkeit, Professionalität, Kundenfokus ausstrahlen. 4 Services sollen präsentiert werden, ggf mit Bildlogo in unterschiedlichen Farben verbinden.

```html
<!DOCTYPE html>
<html lang="de">
<head>
<meta charset="utf-8">
<title>Haldenfels Sàrl – Präsentationsvorlagen</title>
<link rel="stylesheet" href="https://fonts.googleapis.com/css2?family=Cormorant+Garamond:wght@400;500;600&family=Open+Sans:wght@400;600;700&display=swap">
<style>
:root{
  --page:#f7f7f7;
  --panel:#ececec;
  --ink:#2f2f33;
  --slate:#4c5262;
  --slate-mid:#6b7180;
  --slate-light:#9aa0ab;
  --plum:#8b4c71;
  --rule:#b9bcc3;
  --white:#ffffff;
  --label:#222;
}
*{margin:0;padding:0;box-sizing:border-box}
html,body{width:1200px;height:2400px;overflow:hidden}
body{background:linear-gradient(160deg,#fafafa,#f2f2f2);font-family:"Open Sans",Arial,sans-serif;color:var(--ink);position:relative}
.row-label{position:absolute;left:68px;font-size:8px;color:var(--label);font-family:"Open Sans",Arial,sans-serif}
.panel{position:absolute;width:408px;height:238px;background:var(--panel)}
.slide{position:absolute;left:21px;top:15px;width:363px;height:204px;overflow:hidden;background:var(--white);box-shadow:0 1px 4px rgba(0,0,0,.12)}
.photo{position:absolute}
.brand-mini{position:absolute;left:13px;top:14px;font-family:"Open Sans",Arial,sans-serif;font-size:4.6px;letter-spacing:.14em;font-weight:600;color:var(--slate)}
.brand-mini.on-dark{color:var(--white)}
.footer{position:absolute;left:13px;bottom:9px;display:flex;align-items:center;gap:5px;font-size:2.6px;letter-spacing:.12em;font-weight:600;color:var(--slate)}
.footer::before{content:"";width:14px;height:.5px;background:currentColor}
.footer.on-dark{color:#e4e6ea}
.tag{position:absolute;right:14px;top:18px;text-align:right;font-size:3.2px;letter-spacing:.22em;font-weight:600;color:var(--slate);line-height:1.5;padding-right:5px;border-right:1px solid var(--plum)}
.tag.on-dark{color:#c9ccd3}
.page-no{position:absolute;right:7px;top:20px;font-size:3.2px;color:var(--plum)}
.cover-title{position:absolute;right:14px;color:var(--white);font-family:"Open Sans",Arial,sans-serif;font-weight:400;font-size:17px;letter-spacing:.2em;text-align:right;line-height:1.45}
.tiny{font-size:3.1px;line-height:1.55;color:var(--slate)}
.tiny.on-dark{color:#e9eaee}
.brand-center{position:absolute;left:0;right:0;display:flex;justify-content:center;align-items:center;gap:7px;font-family:"Open Sans",Arial,sans-serif;color:var(--slate);font-size:14px;font-weight:600;letter-spacing:.18em}
.brand-dot{width:8px;height:8px;border-radius:50%;background:var(--slate);flex:none}
.svc-title{font-family:"Cormorant Garamond",Georgia,serif;font-size:10.5px;letter-spacing:.06em;line-height:1.2;color:var(--slate)}
.svc-title b{font-weight:600}
.svc-title span{font-weight:400}
.detail{background:var(--white)}
.detail .slate{position:absolute;left:0;top:0;width:347px;height:204px;background:linear-gradient(90deg,#a7abb3 0%,#7b8190 45%,#4f5565 100%)}
.detail .detail-title{position:absolute;text-align:right;color:var(--white);font-family:"Cormorant Garamond",Georgia,serif;font-size:10.5px;letter-spacing:.06em;line-height:1.2}
.detail .detail-title b{font-weight:600}
.detail .copy{position:absolute;left:201px;width:108px}
.qual-h{font-family:"Cormorant Garamond",Georgia,serif;color:var(--plum);font-size:11px;letter-spacing:.04em}
.qual-sub{font-size:3.4px;letter-spacing:.1em;font-weight:600;color:var(--slate);margin:2px 0 5px}
.btn{display:inline-block;border:.6px solid #e5e7eb;color:#fff;font-size:2.8px;letter-spacing:.1em;padding:2px 10px;margin-right:4px}
.contact-row{position:absolute;left:13px;right:13px;bottom:22px;display:flex;justify-content:space-between;align-items:center;font-size:2.5px;letter-spacing:.08em;font-weight:600;color:var(--slate)}
.contact-row span{display:flex;align-items:center;gap:4px}
.contact-row span::before{content:"";width:12px;height:.5px;background:currentColor}
.social-name{font-size:3.4px;font-weight:700;color:var(--slate);letter-spacing:.05em}
</style>
</head>
<body>

<!-- Titel -->
<div class="row-label" style="top:210px">Titel / Start</div>
<div class="panel" style="left:240px;top:95px">
  <div class="slide title-slide" style="background:linear-gradient(150deg,#f4f4f4 0%,#ebebeb 45%,#f6f6f6 70%,#e6e6e6 100%)">
    <div class="photo" role="img" aria-label="Weicher Schattenwurf von Blättern auf heller Wand" style="inset:0;background:linear-gradient(160deg,rgba(255,255,255,0) 40%,rgba(210,210,210,.35) 60%,rgba(255,255,255,0) 75%)"></div>
    <div class="tag" style="top:22px">COMPANY<br>PRESENTATION</div>
    <div class="brand-center" style="top:92px"><span class="brand-dot"></span>HALDENFELS SÀRL</div>
    <div class="footer">FRANKFURT | 2023</div>
  </div>
</div>

<!-- Zusammenfassung -->
<div class="row-label" style="top:557px">Folie / Zusammenfassung</div>
<div class="panel" style="left:240px;top:430px">
  <div class="slide">
    <div class="photo" role="img" aria-label="Grüne gestreifte Calathea-Blätter vor heller Wand" style="inset:0;background:linear-gradient(120deg,#e9ebe6 0%,#f2f2ef 35%,#8fae7a 55%,#4f7a3c 75%,#dfe3da 100%)"></div>
    <div class="brand-mini on-dark">HALDENFELS</div>
    <div class="cover-title" style="top:82px">EXECUTIVE<br>SUMMARY</div>
    <div class="footer">UNTERNEHMENSBERATUNG</div>
  </div>
</div>
<div class="panel" style="left:692px;top:430px">
  <div class="slide" style="background:linear-gradient(180deg,#f8f8f8,#ececec)">
    <div class="photo" role="img" aria-label="Zarte Blattschatten auf weißer Fläche" style="inset:0;background:radial-gradient(ellipse at 70% 20%,rgba(200,200,200,.4),rgba(255,255,255,0) 60%)"></div>
    <div class="brand-mini">HALDENFELS</div>
    <div class="tag">EXECUTIVE<br>SUMMARY</div>
    <div class="page-no">3</div>
    <p class="tiny" style="position:absolute;left:57px;top:70px;width:132px">We support banks, funds and investment firms with clear advice, dependable structures and experienced people. Our work starts with listening and ends with results that last beyond the project itself.<br><br>Each mandate is led by senior partners who know the regulatory field from daily practice. We translate complex rules into simple steps, build the processes that carry them and train the teams who use them every day. Our clients value a partner that stays calm, precise and available.</p>
    <p class="tiny" style="position:absolute;left:205px;top:70px;width:132px">Founded by experts from the financial sector, the firm combines board experience with hands-on project work in several jurisdictions. Our team brings legal, risk and operational knowledge to every assignment.<br><br>From independent mandates to compliance projects, from AML support to coaching, we deliver services that fit the client.<br><br><b>Reliable partners for lasting results.</b></p>
    <div class="footer">UNTERNEHMENSBERATUNG</div>
  </div>
</div>

<!-- Unternehmensvorstellung -->
<div class="row-label" style="top:836px">Folie / Unternehmensvorstellung</div>
<div class="panel" style="left:240px;top:727px">
  <div class="slide">
    <div class="photo" role="img" aria-label="Empfangsbereich eines Büros mit Glaswand, Stehlampe und dunklem Sofa" style="inset:0;background:linear-gradient(100deg,#8c8e92 0%,#b8b9bb 30%,#6e7073 55%,#3f4043 80%,#2b2c2e 100%)"></div>
    <div class="brand-mini on-dark">HALDENFELS</div>
    <div class="cover-title" style="top:84px">ABOUT</div>
    <div class="footer on-dark">UNTERNEHMENSBERATUNG</div>
  </div>
</div>
<div class="panel" style="left:692px;top:727px">
  <div class="slide" style="background:#f4f4f4">
    <div class="photo" role="img" aria-label="Helle Architekturfassade im Gegenlicht" style="inset:0;background:linear-gradient(110deg,#f6f6f6 0%,#ebebeb 45%,#d6d6d6 70%,#f2f2f2 100%)"></div>
    <div class="brand-mini">HALDENFELS</div>
    <div class="tag">QUALIFICATIONS</div>
    <div class="page-no">5</div>
    <div style="position:absolute;left:57px;top:44px;width:120px">
      <div class="qual-h">18+ YEARS</div>
      <div class="qual-sub">OF EXPERIENCE IN THE FINANCIAL SECTOR</div>
      <p class="tiny">Long practice in banking and fund management gives us a sharp view of the risks and duties our clients face every day in a changing market.</p>
      <div style="height:.5px;background:var(--rule);margin:8px 0"></div>
      <div class="qual-sub">QUALIFIED LAWYER</div>
      <p class="tiny">• Admitted to the bar with years of practice<br>• Advisory work in financial regulation<br>• Drafting of policies and governance</p>
    </div>
    <div style="position:absolute;left:205px;top:44px;width:120px">
      <div class="qual-h">10+ YEARS</div>
      <div class="qual-sub">IN EXECUTIVE AND BOARD POSITIONS</div>
      <p class="tiny">Seats on boards of funds and management companies taught us how decisions are made and how sound oversight protects investors and firms.</p>
      <div style="height:.5px;background:var(--rule);margin:8px 0"></div>
      <div class="qual-sub">4 JURISDICTIONS</div>
      <p class="tiny">1) Luxembourg fund structures<br>2) German banking supervision<br>3) Swiss financial market rules<br>4) Irish investment vehicles</p>
    </div>
    <div class="footer">UNTERNEHMENSBERATUNG</div>
  </div>
</div>

<!-- Dienstleistungen -->
<div class="row-label" style="top:1122px">Folie / Dienstleistungen</div>
<div class="panel" style="left:240px;top:1023px">
  <div class="slide">
    <div class="photo" role="img" aria-label="Blick zwischen Hochhauskanten in einen blauen Himmel" style="inset:0;background:linear-gradient(135deg,#4b4e55 0%,#9fb9d2 22%,#5d92c5 50%,#3f7fbe 70%,#6a6d74 100%)"></div>
    <div class="brand-mini on-dark">HALDENFELS</div>
    <div class="cover-title" style="top:70px">SERVICES</div>
    <div class="footer on-dark">UNTERNEHMENSBERATUNG</div>
  </div>
</div>
<div class="panel" style="left:692px;top:1023px">
  <div class="slide" style="background:#f3f3f3">
    <div class="photo" role="img" aria-label="Helle Architektur mit gefalteten Flächen" style="inset:0;background:linear-gradient(120deg,#f7f7f7 0%,#e2e2e2 40%,#f4f4f4 60%,#d9d9d9 100%)"></div>
    <div class="brand-mini">HALDENFELS</div>
    <div class="tag">SERVICES</div>
    <div class="page-no">7</div>
    <svg style="position:absolute;left:58px;top:28px" width="14" height="14" viewBox="0 0 14 14" fill="none" stroke="#8b4c71" stroke-width=".7"><circle cx="7" cy="7" r="5"/><circle cx="7" cy="7" r="2"/></svg>
    <svg style="position:absolute;left:206px;top:28px" width="14" height="14" viewBox="0 0 14 14" fill="none" stroke="#8b4c71" stroke-width=".7"><rect x="3" y="2" width="8" height="10"/><path d="M5 5h4M5 7h4M5 9h3"/></svg>
    <div class="svc-title" style="position:absolute;left:57px;top:48px"><b>INDEPENDENT<br>DIRECTORSHIPS/</b><br><span>RC MANDATES</span></div>
    <div class="svc-title" style="position:absolute;left:205px;top:48px"><b>REGULATORY/<br>COMPLIANCE</b><br><span>SERVICES</span></div>
    <div style="position:absolute;left:57px;top:111px;width:280px;height:.5px;background:var(--slate-mid)"></div>
    <svg style="position:absolute;left:58px;top:117px" width="14" height="14" viewBox="0 0 14 14" fill="none" stroke="#8b4c71" stroke-width=".7"><path d="M2 12l5-5M6 3l5 5M8 2l4 4"/></svg>
    <svg style="position:absolute;left:206px;top:117px" width="14" height="14" viewBox="0 0 14 14" fill="none" stroke="#8b4c71" stroke-width=".7"><circle cx="7" cy="6" r="3.5"/><path d="M5.5 10h3M6 12h2"/></svg>
    <div class="svc-title" style="position:absolute;left:57px;top:136px"><b>AML/CTF</b><br><span>SUPPORT</span></div>
    <div class="svc-title" style="position:absolute;left:205px;top:136px"><b>COACHING/<br>TRAININGS</b></div>
    <div class="footer">UNTERNEHMENSBERATUNG</div>
  </div>
</div>

<!-- Dienstleistung einzeln -->
<div class="row-label" style="top:1659px">Folien / Dienstleistung einzeln</div>
<div class="panel" style="left:240px;top:1408px">
  <div class="slide detail">
    <div class="slate"></div>
    <div class="photo" role="img" aria-label="Tablet und Notizbuch auf einem Schreibtisch" style="left:0;top:0;width:170px;height:204px;background:linear-gradient(90deg,#6c7079 0%,#b4b7bd 45%,rgba(160,164,172,0) 100%)"></div>
    <div class="brand-mini on-dark">HALDENFELS</div>
    <div class="tag on-dark" style="right:18px;border:none">SERVICES</div>
    <div class="page-no" style="right:8px">8</div>
    <div class="detail-title" style="right:164px;top:47px"><b>INDEPENDENT<br>DIRECTORSHIPS/</b><br>RC MANDATES</div>
    <svg style="position:absolute;left:201px;top:73px" width="14" height="14" viewBox="0 0 14 14" fill="none" stroke="#fff" stroke-width=".7"><circle cx="7" cy="7" r="5"/><circle cx="7" cy="7" r="2"/></svg>
    <p class="tiny on-dark copy" style="top:103px">We take on independent board seats and conducting officer roles for funds and management companies. Our directors bring oversight, judgement and a clear voice to the table. They review reports, challenge decisions and protect the interests of investors while keeping a close and open dialogue with management.</p>
    <div class="footer on-dark">UNTERNEHMENSBERATUNG</div>
  </div>
</div>
<div class="panel" style="left:692px;top:1408px">
  <div class="slide detail">
    <div class="slate" style="background:linear-gradient(90deg,#3d4048 0%,#8d919b 30%,#6a7080 60%,#4f5565 100%)"></div>
    <div class="photo" role="img" aria-label="Gebäudefassade mit Raster und Schrägdach" style="left:0;top:0;width:170px;height:204px;background:linear-gradient(90deg,#1e1f22 0%,#55585f 35%,rgba(150,154,162,0) 100%)"></div>
    <div class="brand-mini on-dark">HALDENFELS</div>
    <div class="tag on-dark" style="right:18px;border:none">SERVICES</div>
    <div class="page-no" style="right:8px">9</div>
    <div class="detail-title" style="left:123px;top:47px;text-align:left"><b>AML/CTF</b><br>SUPPORT</div>
    <svg style="position:absolute;left:201px;top:80px" width="14" height="14" viewBox="0 0 14 14" fill="none" stroke="#fff" stroke-width=".7"><path d="M2 12l5-5M6 3l5 5M8 2l4 4"/></svg>
    <p class="tiny on-dark copy" style="top:103px">We help firms meet their duties against money laundering and terrorist financing. This covers risk assessments, client checks and reviews of existing controls.<br><br>Our team supports daily operations, prepares audits and gives clear guidance when cases need a fast and careful decision.</p>
    <div style="position:absolute;left:201px;top:163px"><span class="btn">AML SUPPORT</span><span class="btn">CTF SUPPORT</span></div>
    <div class="footer on-dark">UNTERNEHMENSBERATUNG</div>
  </div>
</div>
<div class="panel" style="left:240px;top:1683px">
  <div class="slide detail">
    <div class="slate"></div>
    <div class="photo" role="img" aria-label="Aufgefächerte Papierseiten in sanftem Licht" style="left:0;top:0;width:170px;height:204px;background:linear-gradient(90deg,#8d9099 0%,#c9cbd0 40%,rgba(170,174,182,0) 100%)"></div>
    <div class="brand-mini on-dark">HALDENFELS</div>
    <div class="tag on-dark" style="right:18px;border:none">SERVICES</div>
    <div class="page-no" style="right:8px">10</div>
    <div class="detail-title" style="right:164px;top:47px"><b>REGULATORY/<br>COMPLIANCE</b><br>SERVICES</div>
    <svg style="position:absolute;left:201px;top:71px" width="14" height="14" viewBox="0 0 14 14" fill="none" stroke="#fff" stroke-width=".7"><rect x="3" y="2" width="8" height="10"/><path d="M5 5h4M5 7h4M5 9h3"/></svg>
    <p class="tiny on-dark copy" style="top:103px">We plan and carry out regulatory projects from the first gap analysis to the final handover. Policies, procedures and reporting are set up to match the rules.<br><br>Our experts stay at your side when new rules arrive and keep your framework current.<br>• clear project plans<br>• reliable reporting<br>• lasting documentation</p>
    <div class="footer on-dark">UNTERNEHMENSBERATUNG</div>
  </div>
</div>
<div class="panel" style="left:692px;top:1683px">
  <div class="slide detail">
    <div class="slate" style="background:linear-gradient(90deg,#c4c6ca 0%,#8d929c 45%,#4f5565 100%)"></div>
    <div class="photo" role="img" aria-label="Bunte Stifte an einer gezeichneten Leiter vor heller Wand" style="left:0;top:110px;width:200px;height:94px;background:linear-gradient(180deg,rgba(120,126,138,0) 0%,#3e7f96 70%,#3c8aa0 100%)"></div>
    <div class="brand-mini on-dark">HALDENFELS</div>
    <div class="tag on-dark" style="right:18px;border:none">SERVICES</div>
    <div class="page-no" style="right:8px">11</div>
    <div class="detail-title" style="left:105px;top:47px;text-align:left"><b>COACHING/<br>TRAININGS</b></div>
    <svg style="position:absolute;left:201px;top:78px" width="14" height="14" viewBox="0 0 14 14" fill="none" stroke="#fff" stroke-width=".7"><circle cx="7" cy="6" r="3.5"/><path d="M5.5 10h3M6 12h2"/></svg>
    <p class="tiny on-dark copy" style="top:103px">Our trainings give teams the knowledge they need for daily work. We design seminars, workshops and coaching for boards, managers and staff, always built around real cases from the client’s business and adapted to each level of experience.</p>
    <svg style="position:absolute;left:201px;top:161px" width="6" height="5" viewBox="0 0 6 5" fill="none" stroke="#fff" stroke-width=".7"><path d="M0 0l2.5 2.5L0 5M3 0l2.5 2.5L3 5"/></svg>
    <p class="tiny on-dark" style="position:absolute;left:209px;top:166px;width:100px;font-size:2.8px;font-weight:600;letter-spacing:.05em">PRACTICAL SESSIONS FOR EVERY TEAM<br>TAILORED CONTENT AND CLEAR GOALS<br>CERTIFIED RESULTS FOR ALL PARTICIPANTS</p>
    <div class="footer on-dark">UNTERNEHMENSBERATUNG</div>
  </div>
</div>

<!-- Kontakt -->
<div class="row-label" style="top:2122px">Folie / Kontakt</div>
<div class="panel" style="left:240px;top:2015px">
  <div class="slide" style="background:#efefef">
    <div class="photo" role="img" aria-label="Helle Kletterwand mit hellen Griffen" style="inset:0;background:radial-gradient(ellipse at 30% 30%,#f7f7f7,#e8e8e8 60%,#e1e1e1 100%)"></div>
    <div class="tag" style="border:none;right:18px">KONTAKT</div>
    <div class="brand-center" style="top:92px"><span class="brand-dot"></span>HALDENFELS SÀRL</div>
    <div class="contact-row">
      <span>VORNAME NAME</span>
      <span>TELEFON 069 4821 377</span>
      <span>E-MAIL INFO@HALDENFELS-BERATUNG.DE</span>
      <span>LINDENALLEE 14</span>
      <span>60311 FRANKFURT</span>
      <b class="social-name">Linkwerk</b>
    </div>
  </div>
</div>

</body>
</html>
```